6 page (for now) squarespace website design for a Mobile Fitness small business

My sons California based small business "BrenVale Coaching" with new subsidiary called "BrenVale 4 Kids". I don't understand coding the website, is that the function squarespace provides?
In the end I want a working website, squarespace, I have a google workspace domain, email and subscription to squarespace & google workspace. URLs include brenvalecoaching.example and brenvale4kids.example. I have an idea of what I am looking for in a website and I have some examples of website designs I like, but I am 100% open to your design concepts and artistic flair. email is torin@brenvalecoaching.example
I am looking for someone to design the site, help me understand how to make "minor" changes and hopefully have a long term relationship on the tech side of the business. I need an Idea of pricing for future changes (Rate T&M).
There are 2 businesses so I need a way to incorporate both the main company and a subsidiary into 1 website or link it somehow. I am open to your suggestions how to accomplish that. Do I need 2 completely separate websites or can it be done on 1 site directing you to different pages. I read conflicting info if it is a BAD idea to link 2 different websites so I will defer to your advice.
Below are the pages I need designed:
- Home Page- BrenVale Coaching
- Home Page- BrenVale 4 Kids (Homeschool market)
- Member Page (subscription service?)
- Workouts- with video clips 1-6 min each
- About
- Contact
- FAQ's
Future work & page designs:
- Store with training subscriptions & a few merch items
- Booking Appointments
- Bookshelf
- email campaign
-Blog
I like the feel of this website:
https://zestlope.example/

```html
<!DOCTYPE html>
<html lang="en">
<head>
<meta charset="utf-8">
<title>BrenVale Coaching</title>
<link href="https://fonts.googleapis.com/css2?family=IBM+Plex+Sans:wght@400;500;600&display=swap" rel="stylesheet">
<style>
:root{
  --ink:#000000;
  --text:#1d1d1d;
  --white:#ffffff;
  --soft:#f5f4f5;
  --footer:#000000;
  --social:#2d7fd6;
}
*{box-sizing:border-box;margin:0;padding:0}
html,body{width:1200px;height:3081px;overflow:hidden}
body{font-family:"IBM Plex Sans",Arial,sans-serif;color:var(--text);background:var(--white);position:relative}
section,header,footer{position:absolute;left:0;width:1200px}
.abs{position:absolute}
h1,h2,h3{font-weight:400}
.btn{position:absolute;display:flex;align-items:center;justify-content:center;background:var(--ink);color:var(--white);font-size:13px;font-weight:500;letter-spacing:.2px}
.photo{position:absolute}

/* hero */
.hero{top:0;height:722px;background:#2a2620}
.hero .photo{inset:0;background:
  radial-gradient(ellipse 230px 200px at 720px 380px,rgba(236,232,226,.75),rgba(236,232,226,0) 70%),
  radial-gradient(ellipse 170px 150px at 760px 240px,rgba(196,150,120,.7),rgba(196,150,120,0) 75%),
  radial-gradient(ellipse 200px 130px at 430px 560px,rgba(40,140,160,.55),rgba(40,140,160,0) 75%),
  radial-gradient(ellipse 260px 140px at 780px 660px,rgba(30,40,80,.85),rgba(30,40,80,0) 75%),
  radial-gradient(ellipse 260px 300px at 1120px 130px,rgba(200,150,60,.55),rgba(200,150,60,0) 75%),
  radial-gradient(ellipse 320px 260px at 200px 220px,rgba(150,140,120,.45),rgba(150,140,120,0) 75%),
  linear-gradient(100deg,#4a4640 0%,#6a5d4c 40%,#4e4539 65%,#3a3025 100%)}
.hero-shade{position:absolute;inset:0;background:linear-gradient(90deg,rgba(0,0,0,.35),rgba(0,0,0,.05) 60%,rgba(0,0,0,.2))}
.brand{position:absolute;color:var(--white);font-weight:400;letter-spacing:6px;display:flex;align-items:center;gap:10px}
.brand-dot{width:14px;height:14px;border-radius:50%;background:var(--white)}
.hero .brand{left:128px;top:104px;font-size:25px}
.nav{position:absolute;display:flex;color:var(--white);font-size:15px;letter-spacing:.2px}
.hero .nav{top:30px;left:543px}
.nav a{color:inherit;text-decoration:none;position:absolute;white-space:nowrap}
.hero-kicker{left:128px;top:407px;font-size:33px;color:var(--white)}
.hero-title{left:128px;top:449px;font-size:52px;color:var(--white);letter-spacing:.5px}
.hero .btn{left:131px;top:525px;width:173px;height:42px;background:var(--white);color:var(--ink);font-size:14.5px;font-weight:400}

/* coaching */
.coaching{top:722px;height:614px;background:var(--white)}
.section-title{position:absolute;left:0;width:1200px;text-align:center;font-size:26px;color:var(--ink);letter-spacing:.3px}
.coaching .section-title{top:46px}
.card-title{position:absolute;width:455px;text-align:center;font-size:22px;color:var(--ink)}
.card-text{position:absolute;width:455px;text-align:center;font-size:14.5px;line-height:19.5px}

/* about */
.about{top:1336px;height:555px;background:var(--soft)}
.about h2{position:absolute;left:642px;top:132px;font-size:29px;color:var(--ink)}
.about p{position:absolute;left:642px;top:193px;width:424px;font-size:14.4px;line-height:22.5px}

/* subscription */
.plans{top:1891px;height:593px;background:var(--white)}
.plans .section-title{top:50px}
.plan-label{position:absolute;width:298px;text-align:center;font-size:21px;color:var(--ink)}

/* newsletter */
.news{top:2484px;height:415px;background:#1c1d20}
.news .photo{inset:0;background:
  radial-gradient(ellipse 200px 230px at 350px 260px,rgba(110,100,90,.55),rgba(110,100,90,0) 75%),
  radial-gradient(ellipse 220px 200px at 860px 190px,rgba(95,90,88,.5),rgba(95,90,88,0) 75%),
  radial-gradient(ellipse 90px 90px at 610px 40px,rgba(140,120,105,.45),rgba(140,120,105,0) 75%),
  linear-gradient(90deg,#18191c,#2b2c30 50%,#1a1b1e)}
.news h2{position:absolute;left:0;width:1200px;top:120px;text-align:center;color:var(--white);font-size:28px;font-weight:500;letter-spacing:.5px}
.news p{position:absolute;left:0;width:1200px;top:163px;text-align:center;color:var(--white);font-size:14.5px}
.signup{position:absolute;left:403px;top:211px;width:392px;height:55px;background:var(--white)}
.signup span{position:absolute;left:18px;top:18px;font-size:14.5px;color:#222}
.signup .btn{left:293px;top:7px;width:90px;height:38px;font-size:14.5px;font-weight:600}

/* footer */
.site-footer{top:2899px;height:182px;background:var(--footer)}
.site-footer .brand{left:130px;top:84px;font-size:18px;letter-spacing:4px}
.site-footer .brand-dot{width:11px;height:11px}
.site-footer .nav{top:67px}
.social{position:absolute;top:122px;width:30px;height:30px;border-radius:50%;background:var(--social)}
.copyright{position:absolute;right:132px;top:126px;color:var(--white);font-size:12px}
</style>
</head>
<body>

<header class="hero">
  <div class="photo" role="img" aria-label="Smiling man doing a kettlebell squat in a gym with two women training behind him"></div>
  <div class="hero-shade"></div>
  <div class="brand"><span class="brand-dot"></span>BRENVALE</div>
  <nav class="nav">
    <a style="left:0">HOME</a>
    <a style="left:78px">MEMBER</a>
    <a style="left:177px">WORKOUTS</a>
    <a style="left:296px">ABOUT</a>
    <a style="left:387px">FAQ'S</a>
    <a style="left:462px">CONTACT</a>
  </nav>
  <div class="abs hero-kicker">WELOME TO</div>
  <h1 class="abs hero-title">BRENVALE COACHING</h1>
  <a class="btn">BOOK APPOINTMENT</a>
</header>

<section class="coaching">
  <h2 class="section-title">OUR COACHING</h2>
  <div class="photo" style="left:130px;top:115px;width:455px;height:276px;background:radial-gradient(ellipse 120px 80px at 230px 110px,rgba(140,150,160,.7),rgba(140,150,160,0) 75%),radial-gradient(ellipse 110px 70px at 370px 130px,rgba(150,100,80,.6),rgba(150,100,80,0) 75%),linear-gradient(180deg,#8a6a4c 0%,#b79a7c 30%,#7d8795 65%,#4f5a6a 100%)" role="img" aria-label="Woman and man doing push-ups on kettlebells in a gym"></div>
  <div class="photo" style="left:615px;top:115px;width:455px;height:276px;background:radial-gradient(ellipse 90px 110px at 250px 130px,rgba(210,90,80,.55),rgba(210,90,80,0) 75%),radial-gradient(ellipse 60px 60px at 250px 90px,rgba(230,190,40,.6),rgba(230,190,40,0) 75%),radial-gradient(ellipse 110px 60px at 180px 250px,rgba(70,150,200,.55),rgba(70,150,200,0) 75%),linear-gradient(90deg,#a3a7aa 0%,#8f8c88 45%,#8a5a48 80%,#5c4a42 100%)" role="img" aria-label="Kids training with suspension straps in a gym"></div>
  <h3 class="card-title" style="left:130px;top:417px">BrenVale Coaching</h3>
  <p class="card-text" style="left:130px;top:458px">There are many variations of passages of Lorem Ipsum<br>available, but the majority have suffered alteration.</p>
  <a class="btn" style="left:304px;top:517px;width:108px;height:37px">READ MORE</a>
  <h3 class="card-title" style="left:615px;top:417px">BrenVale 4 Kids</h3>
  <p class="card-text" style="left:615px;top:458px">There are many variations of passages of Lorem Ipsum<br>available, but the majority have suffered alteration.</p>
  <a class="btn" style="left:789px;top:517px;width:108px;height:37px">READ MORE</a>
</section>

<section class="about">
  <div class="photo" style="left:130px;top:43px;width:456px;height:464px;background:radial-gradient(ellipse 120px 170px at 250px 230px,rgba(80,130,170,.75),rgba(80,130,170,0) 75%),radial-gradient(ellipse 80px 50px at 200px 40px,rgba(230,240,250,.6),rgba(230,240,250,0) 75%),radial-gradient(ellipse 200px 60px at 280px 420px,rgba(15,25,40,.8),rgba(15,25,40,0) 75%),linear-gradient(150deg,#6d8aa6,#3a5878 50%,#1d3049)" role="img" aria-label="Boy doing a dumbbell row on a bench in a gym"></div>
  <h2>ABOUT US</h2>
  <p>Sed ut perspiciatis unde omnis iste natus error sit voluptatem accusantium doloremque laudantium, totam rem aperiam, eaque ipsa quae ab illo inventore veritatis et quasi architecto beatae vitae dicta sunt explicabo. Nemo enim ipsam voluptatem quia voluptas sit aspernatur aut odit aut fugit, sed quia consequuntur magni dolores eos qui ratione voluptatem sequi nesciunt.</p>
  <a class="btn" style="left:645px;top:366px;width:108px;height:37px">READ MORE</a>
</section>

<section class="plans">
  <h2 class="section-title">SUBSCRIPTION</h2>
  <div class="photo" style="left:129px;top:122px;width:298px;height:313px;background:radial-gradient(ellipse 70px 90px at 150px 130px,rgba(110,115,120,.6),rgba(110,115,120,0) 75%),radial-gradient(ellipse 130px 40px at 150px 205px,rgba(40,55,90,.45),rgba(40,55,90,0) 75%),linear-gradient(180deg,#e6ebee 0%,#b9c2c8 45%,#dfe6ea 70%,#c8d3da 100%)" role="img" aria-label="Girl training on suspension straps in a bright gym"></div>
  <div class="photo" style="left:450px;top:122px;width:299px;height:313px;background:radial-gradient(ellipse 130px 70px at 130px 170px,rgba(170,40,45,.6),rgba(170,40,45,0) 75%),radial-gradient(ellipse 50px 120px at 260px 170px,rgba(200,200,200,.35),rgba(200,200,200,0) 75%),linear-gradient(180deg,#3c3c3e,#57504f 50%,#2b2b2d)" role="img" aria-label="Two people training with battle ropes"></div>
  <div class="photo" style="left:771px;top:122px;width:299px;height:313px;background:radial-gradient(ellipse 90px 100px at 120px 190px,rgba(245,245,245,.75),rgba(245,245,245,0) 75%),radial-gradient(ellipse 60px 70px at 250px 150px,rgba(235,140,130,.55),rgba(235,140,130,0) 75%),radial-gradient(ellipse 110px 60px at 150px 20px,rgba(230,190,120,.6),rgba(230,190,120,0) 75%),linear-gradient(170deg,#7d7062,#c4ac96 50%,#727780)" role="img" aria-label="Smiling women lifting dumbbells in a group class"></div>
  <div class="plan-label" style="left:129px;top:458px">3 MONTHS</div>
  <div class="plan-label" style="left:450px;top:458px">6 MONTHS</div>
  <div class="plan-label" style="left:771px;top:458px">1 YEAR</div>
  <a class="btn" style="left:224px;top:501px;width:108px;height:37px">READ MORE</a>
  <a class="btn" style="left:546px;top:501px;width:108px;height:37px">READ MORE</a>
  <a class="btn" style="left:867px;top:501px;width:108px;height:37px">READ MORE</a>
</section>

<section class="news">
  <div class="photo" role="img" aria-label="Dimmed photo of a woman and man giving a high five during a plank in a gym"></div>
  <h2>NEWSLETTER SUBSCRIBE</h2>
  <p>Don't miss a thing. Sign up to receive news and updates.</p>
  <div class="signup"><span>Email Address</span><a class="btn">SIGNUP</a></div>
</section>

<footer class="site-footer">
  <div class="brand"><span class="brand-dot"></span>BRENVALE</div>
  <nav class="nav" style="left:577px">
    <a style="left:0">HOME</a>
    <a style="left:75px">MEMBER</a>
    <a style="left:164px">WORKOUTS</a>
    <a style="left:275px">ABOUT</a>
    <a style="left:360px">FAQ'S</a>
    <a style="left:429px">CONTACT</a>
  </nav>
  <span class="social" style="left:129px"></span>
  <span class="social" style="left:167px"></span>
  <span class="social" style="left:209px"></span>
  <div class="copyright">Copyright © 2022 All Rights Reserved</div>
</footer>

</body>
</html>
```